BUSINESS CARD FOR GUITAR SCHOOL

I would like to design a business card for my Guitar Music School. The school is called "Pluck & Lantern".

The card should be yellow.

Target Market(s)

18-35 years old

Industry/Entity Type

School

Contact Information for Business Card

I would like to design a business card for my Guitar Music School. The school is called "Pluck & Lantern". The card should be yellow.

Card must be consistent with my website design: www.pluckandlantern.com.sg

Requirements
Must have
• 1) Name of Company
• 2) Company Logo
• 3) Name of Employee
• 4) Position of Employee
• 5) Contact Number
• 6) Address
Nice to have
• Creative Design
• Card must be consistent with my website design: www.pluckandlantern.com.sg
Should not have
• Boring Design

```html
<!DOCTYPE html>
<html lang="en">
<head>
<meta charset="utf-8">
<title>Pluck &amp; Lantern — Business Card</title>
<link href="https://fonts.googleapis.com/css2?family=Poppins:wght@800&family=Open+Sans:wght@400;700&display=swap" rel="stylesheet">
<style>
  :root {
    --backdrop: #e9e6e1;
    --card-yellow: #f8d90f;
    --card-white: #ffffff;
    --ink: #111111;
    --ink-soft: #4a4a4a;
    --accent-line: #f3dc5a;
  }
  * { box-sizing: border-box; margin: 0; padding: 0; }
  html, body { width: 1200px; height: 913px; overflow: hidden; }
  body {
    background: var(--backdrop);
    position: relative;
    font-family: "Open Sans", Arial, sans-serif;
  }
  .card {
    position: absolute;
    width: 560px;
    height: 320px;
    border-radius: 4px;
    box-shadow: 0 6px 18px rgba(0,0,0,0.18);
    overflow: hidden;
  }
  .card--front {
    left: 60px; top: 130px;
    background: var(--card-yellow);
    display: flex; align-items: center; justify-content: center; gap: 16px;
  }
  .card--back {
    left: 580px; top: 460px;
    background: var(--card-white);
  }
  .brand-name {
    font-family: "Poppins", Arial, sans-serif;
    font-weight: 800;
    color: var(--ink);
    line-height: 1;
    letter-spacing: -0.5px;
  }
  .card--front .brand-name { font-size: 50px; }
  .brand-dot {
    width: 34px; height: 34px; border-radius: 50%;
    background: var(--ink);
    flex: none;
  }
  .back-brand {
    position: absolute; left: 0; top: 0; width: 250px; height: 100%;
    display: flex; align-items: center; justify-content: center;
  }
  .back-brand .brand-name { font-size: 25px; }
  .divider {
    position: absolute; left: 250px; top: 40px; bottom: 40px;
    width: 1px; background: var(--accent-line);
  }
  .contact {
    position: absolute; left: 280px; top: 44px; right: 24px;
    color: var(--ink-soft);
  }
  .person-name { font-weight: 700; font-size: 15px; color: #333; }
  .person-role { font-size: 11px; margin-top: 2px; }
  .address { font-size: 11px; line-height: 1.45; margin-top: 72px; }
  .contact-list { list-style: none; margin-top: 4px; font-size: 11px; line-height: 1.6; }
  .contact-list li { display: flex; align-items: center; gap: 8px; }
  .contact-list li:last-child { color: var(--ink); font-weight: 700; }
  .icon { width: 10px; height: 10px; flex: none; }
</style>
</head>
<body>
  <section class="card card--front" aria-label="Card front">
    <span class="brand-dot"></span>
    <span class="brand-name">Pluck &amp; Lantern</span>
  </section>

  <section class="card card--back" aria-label="Card back">
    <div class="back-brand"><span class="brand-name">Pluck &amp; Lantern</span></div>
    <div class="divider"></div>
    <div class="contact">
      <p class="person-name">Your Long Name</p>
      <p class="person-role">Managing Director</p>
      <p class="address">27 Kembangan Lane Harbour Building<br>B #05-03 Singapore 418822</p>
      <ul class="contact-list">
        <li>
          <svg class="icon" viewBox="0 0 10 10"><path d="M2 1 L4 1 L4.5 3 L3.3 4 Q4.5 6 6 6.7 L7 5.5 L9 6 L9 8 Q5 9 2 6 Q0.5 3.5 2 1Z" fill="#e0c200"/></svg>
          +65 91234567
        </li>
        <li>
          <svg class="icon" viewBox="0 0 10 10"><rect x="0.5" y="2" width="9" height="6" rx="1" fill="#e0c200"/><path d="M1 2.5 L5 5.5 L9 2.5" stroke="#fff" stroke-width="0.8" fill="none"/></svg>
          yourname@pluckandlantern.com.sg
        </li>
        <li>
          <svg class="icon" viewBox="0 0 10 10"><circle cx="5" cy="5" r="4.3" fill="#e0c200"/><path d="M1 5 H9 M5 0.8 Q2.5 5 5 9.2 Q7.5 5 5 0.8" stroke="#fff" stroke-width="0.7" fill="none"/></svg>
          www.pluckandlantern.com.sg
        </li>
      </ul>
    </div>
  </section>
</body>
</html>
```